OrvanoGoodsHub.com -Ecommerce Website for Luxury Products

This will be an ecommerce site. A website portal that will allow both consumers to enter one way and see specific purchase options and businesses to enter via a different link that allows B2B to see their specific options once logged into. B2C can purchase both as a guest/or after account is setup. B2B must be approved to set up account. This is front end website project. Back-end integration is separate. Will be hosted on Servantia with a domain registration held at Pexadrinet. Additional website concept/idea/synergy can be found from sister site-KRWZHospitality.com

```html
<!DOCTYPE html>
<html lang="en">
<head>
<meta charset="utf-8">
<title>OrvanoGoodsHub — Purveyors of Luxury Lifestyle Accoutrements</title>
<link href="https://fonts.googleapis.com/css2?family=Cinzel:wght@400;500;600;700&family=Poppins:wght@300;400;500&family=Cormorant+Garamond:ital@1&display=swap" rel="stylesheet">
<style>
:root{
  --gold:#c9a94f;
  --gold-deep:#b8953c;
  --dark:#1e130c;
  --ink:#1b1b1b;
  --muted:#555;
  --white:#fff;
}
*{margin:0;padding:0;box-sizing:border-box}
html,body{width:1200px;height:4717px;overflow:hidden}
body{position:relative;background:var(--white);font-family:'Poppins',sans-serif;color:var(--ink)}
.btn{position:absolute;background:var(--gold);color:#fff;font-size:13px;font-weight:500;text-transform:uppercase;border-radius:22px;display:flex;align-items:center;justify-content:center;letter-spacing:.2px}
.photo{position:absolute;overflow:hidden}

/* hero */
.hero{position:absolute;left:0;top:0;width:1200px;height:1222px;background:
 radial-gradient(ellipse 170px 150px at 830px 470px,#9a7440 0%,rgba(90,60,30,.6) 45%,transparent 80%),
 radial-gradient(ellipse 130px 110px at 680px 330px,#8a6a3a 0%,rgba(80,55,28,.5) 50%,transparent 85%),
 radial-gradient(ellipse 260px 220px at 1010px 250px,#6e4222 0%,#4a2a16 45%,transparent 85%),
 radial-gradient(ellipse 560px 300px at 800px 560px,#3e2616 0%,transparent 80%),
 linear-gradient(180deg,#24160d 0%,#1a100a 60%,#1d120b 100%)}
.brand{position:absolute;left:110px;width:268px;text-align:center}
.brand .mark{width:14px;height:14px;border-radius:50%;background:var(--gold);margin:0 auto 10px}
.brand .name{font-family:'Cinzel',serif;font-size:27px;color:var(--gold);letter-spacing:.5px}
.brand .div{font-family:'Cinzel',serif;font-size:8.5px;color:var(--gold);letter-spacing:2px;margin-top:1px}
.brand .tag{font-family:'Cormorant Garamond',serif;font-style:italic;font-size:13px;color:var(--gold);margin-top:8px;text-align:left}
.nav{position:absolute;top:100px;left:462px;font-size:13px;text-transform:uppercase}
.nav a{position:absolute;white-space:nowrap;color:#fff;text-decoration:none}
.nav a.active{color:var(--gold)}
.icon-btn{position:absolute;top:41px;width:38px;height:38px;border-radius:50%;display:flex;align-items:center;justify-content:center}
.hero-title{position:absolute;left:110px;color:#fff;font-family:'Cinzel',serif;line-height:1}
.hero-p{position:absolute;left:110px;top:543px;width:520px;color:#f2ece4;font-size:15px;line-height:29px}
.divider{position:absolute;height:1px;background:var(--gold-deep);opacity:.8}
.dot{position:absolute;width:16px;height:16px;border-radius:50%;background:var(--gold)}
.section-title{position:absolute;left:0;width:1200px;text-align:center;font-family:'Cinzel',serif}
.center-p{position:absolute;left:0;width:1200px;text-align:center;font-size:13.5px;line-height:26px}
.cat{position:absolute;top:984px;width:160px;text-align:center;font-size:13px;line-height:21px;color:#fff}
.cat .circle{width:88px;height:88px;border-radius:50%;background:var(--gold);margin:0 auto 18px;display:flex;align-items:center;justify-content:center;box-shadow:0 6px 14px rgba(0,0,0,.35)}
.cat.on .circle{background:#fff}
.cat.on{color:var(--gold)}

/* content */
.frame{position:absolute;border:2px solid var(--gold);border-radius:36px}
.card{border-radius:36px;box-shadow:0 14px 30px rgba(0,0,0,.28)}
.h2{position:absolute;font-family:'Cinzel',serif;font-size:36px;line-height:46px;color:var(--ink);letter-spacing:.3px;font-weight:600}
.body-p{position:absolute;font-size:12.5px;line-height:28.5px;color:var(--muted);text-align:justify}
.tile{position:absolute;width:233px;height:304px;border-radius:22px;overflow:hidden}
.tile-label{position:absolute;width:233px;text-align:center;font-size:14px;color:var(--ink);font-weight:500}
.concierge{position:absolute;left:0;top:2452px;width:1200px;height:610px;background:
 radial-gradient(ellipse 120px 110px at 850px 420px,#c56a1c 0%,#7a3a12 45%,transparent 85%),
 radial-gradient(ellipse 240px 70px at 900px 300px,#4a3022 0%,transparent 85%),
 radial-gradient(ellipse 300px 70px at 480px 500px,#6a4024 0%,transparent 85%),
 radial-gradient(ellipse 220px 160px at 110px 290px,rgba(200,140,50,.35) 0%,transparent 80%),
 radial-gradient(ellipse 700px 90px at 600px 590px,#3a2a22 0%,transparent 85%),
 linear-gradient(180deg,#1b1612 0%,#15100c 100%)}
.checks{position:absolute;left:143px;top:3440px;list-style:none;font-size:14px;color:var(--gold-deep)}
.checks li{position:relative;height:31px;display:flex;align-items:center}
.checks li svg{position:absolute;left:-29px}

/* footer */
.footer{position:absolute;left:0;top:4282px;width:1200px;height:435px;background:linear-gradient(180deg,#22150d,#1a100a)}
.f-col{position:absolute;top:4362px;color:#fff;font-size:13.5px}
.f-col h4{font-family:'Cinzel',serif;font-weight:400;font-size:19px;color:var(--gold);margin-bottom:18px}
.f-col p{height:34px}
.f-col .lbl{color:var(--gold)}
.legal{position:absolute;top:4669px;font-size:11px;color:#fff}
</style>
</head>
<body>

<div class="hero" role="img" aria-label="Dark still life of a leather bag, perfume bottle, wristwatch in a box and cigars on a wooden surface"></div>

<div class="brand" style="top:42px">
  <div class="mark"></div>
  <div class="name">ORVANOGOODSHUB</div>
  <div class="div">A DIVISION OF KRWZ HOSPITALITY</div>
  <div class="tag">Purveyors of Luxury Lifestyle Accoutrements</div>
</div>

<nav class="nav">
  <a class="active" style="left:0">Home</a>
  <a style="left:87px">About Us</a>
  <a style="left:198px">Retail Collections</a>
  <a style="left:380px">Wholesale Portal</a>
  <a style="left:558px">Partners</a>
</nav>

<div class="btn" style="left:818px;top:42px;width:118px;height:36px;font-size:12px">Contact Us</div>
<div class="icon-btn" style="left:953px;background:var(--gold)">
  <svg width="14" height="14" viewBox="0 0 14 14"><circle cx="7" cy="4.5" r="3" fill="#fff"/><path d="M1.5 13c0-3 2.5-5 5.5-5s5.5 2 5.5 5z" fill="#fff"/></svg>
</div>
<div class="icon-btn" style="left:1001px;background:#fff">
  <svg width="14" height="13" viewBox="0 0 14 13"><path d="M7 12L1.6 6.6A3 3 0 0 1 7 2.4a3 3 0 0 1 5.4 4.2z" fill="none" stroke="#c9a94f" stroke-width="1.4"/></svg>
</div>
<div class="icon-btn" style="left:1049px;background:#fff">
  <svg width="15" height="14" viewBox="0 0 15 14"><path d="M1 1h2.2l1.6 8h7.4l1.6-5.6H4" fill="none" stroke="#c9a94f" stroke-width="1.5"/><circle cx="5.5" cy="12" r="1.2" fill="#c9a94f"/><circle cx="11.5" cy="12" r="1.2" fill="#c9a94f"/></svg>
</div>

<div class="hero-title" style="top:298px;font-size:33px">PURVEYORS OF</div>
<div class="hero-title" style="top:338px;font-size:76px;font-weight:700">LUXURY</div>
<div class="hero-title" style="top:412px;font-size:76px;font-weight:700">LIFESTYLE</div>
<div class="hero-title" style="top:488px;font-size:47px">ACCOUTREMENTS</div>
<p class="hero-p">Curated collections for discerning individuals and elevated solutions for lounges, hospitality, and licensed partners.</p>
<div class="btn" style="left:110px;top:619px;width:256px;height:41px">Shop Retail Collections</div>

<div class="divider" style="left:110px;top:779px;width:448px"></div>
<div class="dot" style="left:592px;top:771px"></div>
<div class="divider" style="left:642px;top:779px;width:446px"></div>

<h2 class="section-title" style="top:843px;font-size:31px;color:var(--gold);font-weight:400">CURATED LUXURY, DEFINED BY CRAFT</h2>
<p class="center-p" style="top:891px;color:#fff;font-size:13px">OrvanoGoodsHub exists at the intersection of craftsmanship, indulgence, and presentation. Every product is selected<br>for its quality, design integrity, and ability to elevate personal rituals or professional environments.</p>

<div class="cat" style="left:252px"><div class="circle">
  <svg width="44" height="44" viewBox="0 0 44 44"><g transform="rotate(-40 22 22)"><rect x="6" y="18" width="32" height="8" rx="4" fill="#fff"/><rect x="28" y="18" width="3" height="8" fill="#c9a94f"/></g></svg>
</div>Cigar &amp; Lounge<br>Accessories</div>
<div class="cat on" style="left:426px"><div class="circle">
  <svg width="40" height="44" viewBox="0 0 40 44"><rect x="16" y="4" width="8" height="7" rx="1.5" fill="#c9a94f"/><rect x="8" y="12" width="24" height="28" rx="6" fill="#c9a94f"/><rect x="13" y="20" width="14" height="10" rx="2" fill="#fff"/></svg>
</div>Fragrances &amp;<br>Oils</div>
<div class="cat" style="left:600px"><div class="circle">
  <svg width="40" height="46" viewBox="0 0 40 46"><path d="M13 4h14l-4 7h-6z" fill="#fff"/><path d="M17 12h6l5 22-8 8-8-8z" fill="#fff"/></svg>
</div>Attire &amp; Lifestyle<br>Accessories</div>
<div class="cat" style="left:774px"><div class="circle">
  <svg width="44" height="40" viewBox="0 0 44 40"><path d="M10 4h24l8 10-20 24L2 14z" fill="#fff"/><path d="M2 14h40M16 4l-4 10 10 24 10-24-4-10" fill="none" stroke="#c9a94f" stroke-width="1.5"/></svg>
</div>Limited &amp; Exclusive<br>Releases</div>

<!-- elevating -->
<div class="frame" style="left:110px;top:1392px;width:421px;height:409px"></div>
<div class="photo card" style="left:147px;top:1337px;width:445px;height:427px;background:
 radial-gradient(ellipse 90px 70px at 100px 70px,#5e6a36 0%,transparent 80%),
 radial-gradient(ellipse 200px 120px at 240px 170px,#b27a48 0%,#8a5530 45%,transparent 85%),
 radial-gradient(ellipse 120px 90px at 360px 260px,#a8412a 0%,transparent 80%),
 radial-gradient(ellipse 180px 100px at 150px 320px,#7a6a38 0%,transparent 85%),
 linear-gradient(160deg,#3a2414 0%,#6a4226 45%,#2a180c 100%)" role="img" aria-label="Bundle of cigars resting on tobacco leaves beside a decorative tin"></div>

<h2 class="h2" style="left:692px;top:1357px">ELEVATING<br>LIFESTYLE THROUGH<br>CRAFTSMANSHIP</h2>
<p class="body-p" style="left:692px;top:1508px;width:396px">OrvanoGoodsHub exists at the intersection of craftsmanship, indulgence, and presentation. Every product is selected for its quality, design integrity, and ability to elevate personal rituals or professional environments.</p>
<p class="body-p" style="left:692px;top:1650px;width:396px">From private collections to premium lounges, OrvanoGoodsHub delivers refinement with intention.</p>
<div class="btn" style="left:692px;top:1728px;width:138px;height:41px">Read More</div>

<!-- featured -->
<h2 class="section-title" style="top:1910px;font-size:34px;font-weight:600">FEATURED COLLECTIONS</h2>
<p class="center-p" style="top:1952px;color:#444;font-size:14px">Each collection is curated to reflect timeless style, functionality, and understated luxury.</p>

<div class="tile" style="left:112px;top:2008px;background:
 radial-gradient(ellipse 70px 130px at 170px 90px,rgba(190,150,140,.45) 0%,transparent 80%),
 radial-gradient(ellipse 120px 100px at 90px 120px,#9a6a3e 0%,transparent 80%),
 radial-gradient(ellipse 110px 30px at 120px 240px,#8a5a32 0%,transparent 85%),
 linear-gradient(160deg,#3a2012,#5a3820 55%,#1e120a)" role="img" aria-label="Lit cigar with rising smoke on tobacco leaves"></div>
<div class="tile" style="left:359px;top:2008px;background:
 radial-gradient(ellipse 60px 50px at 70px 150px,#f2c060 0%,transparent 80%),
 radial-gradient(ellipse 90px 110px at 150px 170px,#b08a3e 0%,transparent 80%),
 radial-gradient(ellipse 120px 60px at 180px 60px,#d0c2a8 0%,transparent 85%),
 radial-gradient(ellipse 140px 60px at 110px 270px,#3a3a38 0%,transparent 85%),
 linear-gradient(160deg,#5a4a3a,#7a6244 55%,#2b2118)" role="img" aria-label="Essential oil bottles, diffuser reeds, candles and spa stones"></div>
<div class="tile" style="left:606px;top:2008px;background:
 radial-gradient(ellipse 90px 70px at 60px 60px,#c8803a 0%,transparent 80%),
 radial-gradient(ellipse 70px 80px at 190px 90px,#9a5a2a 0%,transparent 80%),
 radial-gradient(ellipse 150px 70px at 120px 230px,#6a3a1e 0%,transparent 85%),
 linear-gradient(160deg,#2a1a10,#4a2a16 50%,#1a110a)" role="img" aria-label="Dim lounge bar interior with leather seating"></div>
<div class="btn" style="left:651px;top:2287px;width:143px;height:31px;font-size:11px">View Products</div>
<div class="tile" style="left:855px;top:2008px;background:
 radial-gradient(ellipse 50px 70px at 190px 110px,#c8a070 0%,transparent 80%),
 radial-gradient(ellipse 130px 50px at 100px 150px,#2a1a14 0%,transparent 85%),
 radial-gradient(ellipse 120px 60px at 110px 230px,#7a3a22 0%,transparent 85%),
 linear-gradient(160deg,#4a2414,#6e3a20 55%,#24140b)" role="img" aria-label="Watches in a display box with a whisky decanter and leather wallet"></div>

<div class="tile-label" style="left:112px;top:2331px">Cigar &amp; Lounge Accessories</div>
<div class="tile-label" style="left:359px;top:2331px">Fragrances &amp; Oils</div>
<div class="tile-label" style="left:606px;top:2331px">Attire &amp; Lifestyle Accessories</div>
<div class="tile-label" style="left:855px;top:2331px">Limited &amp; Exclusive Releases</div>

<!-- concierge -->
<div class="concierge" role="img" aria-label="Cigars and a glass of whisky on ice against a dark backdrop with warm bokeh lights"></div>
<h2 class="section-title" style="top:2524px;font-size:35px;color:#fff;font-weight:600">CONCIERGE &amp; CUSTOM INQUIRIES</h2>
<p class="center-p" style="top:2577px;color:#fff;font-size:15.5px;line-height:29px">Questions about products, bulk orders, or custom sourcing? Our concierge team is<br>available to assist both private clients and business partners.</p>
<div class="btn" style="left:493px;top:2655px;width:214px;height:40px">Contact Concierge</div>

<!-- solutions -->
<h2 class="h2" style="left:112px;top:3181px">LUXURY SOLUTIONS<br>FOR LOUNGES &amp;<br>BUSINESSES</h2>
<p class="body-p" style="left:112px;top:3333px;width:396px">OrvanoGoodsHub partners with lounges, hospitality groups, and licensed businesses seeking products that enhance brand perception and customer experience.</p>
<ul class="checks">
  <li><svg width="16" height="16" viewBox="0 0 16 16"><circle cx="8" cy="8" r="8" fill="#c9a94f"/><path d="M4.5 8.2l2.3 2.3 4.7-4.8" fill="none" stroke="#fff" stroke-width="1.6"/></svg>Trade-only pricing</li>
  <li><svg width="16" height="16" viewBox="0 0 16 16"><circle cx="8" cy="8" r="8" fill="#c9a94f"/><path d="M4.5 8.2l2.3 2.3 4.7-4.8" fill="none" stroke="#fff" stroke-width="1.6"/></svg>Curated assortments</li>
  <li><svg width="16" height="16" viewBox="0 0 16 16"><circle cx="8" cy="8" r="8" fill="#c9a94f"/><path d="M4.5 8.2l2.3 2.3 4.7-4.8" fill="none" stroke="#fff" stroke-width="1.6"/></svg>Bulk and recurring orders</li>
  <li><svg width="16" height="16" viewBox="0 0 16 16"><circle cx="8" cy="8" r="8" fill="#c9a94f"/><path d="M4.5 8.2l2.3 2.3 4.7-4.8" fill="none" stroke="#fff" stroke-width="1.6"/></svg>Concierge-level support</li>
</ul>
<div class="btn" style="left:112px;top:3587px;width:138px;height:41px">Read More</div>

<div class="frame" style="left:641px;top:3239px;width:447px;height:401px"></div>
<div class="photo card" style="left:606px;top:3180px;width:447px;height:426px;background:
 radial-gradient(ellipse 80px 110px at 310px 260px,#d08a30 0%,#8a4a16 50%,transparent 85%),
 radial-gradient(ellipse 220px 60px at 240px 100px,rgba(220,150,60,.45) 0%,transparent 85%),
 radial-gradient(ellipse 160px 70px at 130px 230px,#5a3018 0%,transparent 85%),
 radial-gradient(ellipse 260px 70px at 220px 380px,#2e2018 0%,transparent 85%),
 linear-gradient(180deg,#2a180c 0%,#3a2212 50%,#1a110a 100%)" role="img" aria-label="Glass of whisky and a cigar on a table in a warmly lit lounge"></div>

<!-- craft -->
<h2 class="section-title" style="top:3735px;font-size:34px;font-weight:600">WHERE CRAFT MEETS LIFESTYLE</h2>
<p class="center-p" style="top:3777px;color:#444;font-size:14px">Each collection is curated to reflect timeless style, functionality, and understated luxury.</p>

<div class="tile" style="left:112px;top:3836px;height:297px;background:
 radial-gradient(ellipse 100px 60px at 115px 150px,#8a4a34 0%,transparent 80%),
 radial-gradient(ellipse 90px 40px at 110px 280px,#4a2a1a 0%,transparent 85%),
 linear-gradient(160deg,#120a06,#2a1810 55%,#1a100a)" role="img" aria-label="Hands cutting a cigar"></div>
<div class="tile" style="left:359px;top:3836px;height:297px;background:
 radial-gradient(ellipse 90px 70px at 150px 80px,#b07a50 0%,transparent 80%),
 radial-gradient(ellipse 140px 80px at 110px 210px,#8a5a34 0%,transparent 85%),
 linear-gradient(160deg,#2a1a10,#5a3a22 55%,#1e130b)" role="img" aria-label="Hands rolling cigars on a wooden workbench"></div>
<div class="tile" style="left:606px;top:3836px;height:297px;background:
 radial-gradient(ellipse 110px 90px at 120px 160px,#6a4226 0%,transparent 85%),
 radial-gradient(ellipse 50px 80px at 70px 150px,#8a5a2e 0%,transparent 80%),
 linear-gradient(160deg,#140d08,#2e1e12 55%,#120b07)" role="img" aria-label="Row of assorted cigars standing upright"></div>
<div class="tile" style="left:855px;top:3836px;height:297px;background:
 radial-gradient(ellipse 60px 60px at 160px 90px,#c08040 0%,transparent 80%),
 radial-gradient(ellipse 130px 70px at 100px 200px,#6a3e20 0%,transparent 85%),
 linear-gradient(160deg,#1e120a,#3a2212 55%,#140c07)" role="img" aria-label="Open wooden cigar box with a pen on a desk"></div>
<div class="btn" style="left:469px;top:4170px;width:264px;height:40px">Discover the Collection</div>

<!-- footer -->
<footer class="footer"></footer>
<div class="brand" style="top:4368px">
  <div class="mark"></div>
  <div class="name">ORVANOGOODSHUB</div>
  <div class="div">A DIVISION OF KRWZ HOSPITALITY</div>
  <div class="tag">Purveyors of Luxury Lifestyle Accoutrements</div>
</div>

<div class="f-col" style="left:463px">
  <h4>QUICK LINKS</h4>
  <p>Home</p><p>About Us</p><p>Retail Collections</p><p>Wholesale Portal</p><p>Partner</p>
</div>
<div class="f-col" style="left:670px">
  <h4>HELP LINKS</h4>
  <p>Contact &amp; Concierge</p><p>Support</p><p>Custom Orders</p><p>B2B Inquiries</p>
</div>
<div class="f-col" style="left:874px">
  <h4>CONTACT INFO</h4>
  <p>OrvanoGoodsHub</p><p>48 Larkspur Row, Suite 12</p><p>Fernvale, ST 00410, USA</p>
  <p><span class="lbl">Tel:</span> +1 555 014 2290</p>
  <p><span class="lbl">E-mail:</span> info@orvanogoodshub.com</p>
</div>

<div class="divider" style="left:110px;top:4627px;width:448px"></div>
<div class="dot" style="left:592px;top:4619px"></div>
<div class="divider" style="left:642px;top:4627px;width:446px"></div>

<div class="legal" style="left:110px">(C) Copyright 2026 | All Rights Reserved</div>
<div class="legal" style="left:874px;width:214px;text-align:right">Journal &nbsp;&nbsp;|&nbsp;&nbsp; Gallery &nbsp;&nbsp;|&nbsp;&nbsp; Films</div>

</body>
</html>
```